Project Overview:
We are looking to create a website for a monthly subscription IPTV service in WordPress. The website should provide a seamless user experience for customers to sign up for the service and manage their account information. We need the following pages: Home Page, Product Page, Sign-Up Page, and Account Information Page.

Home Page:
The Home Page design should be simple and clean, with a dark theme and minimalistic design elements. We would like to include graphics of popular movie shows displayed on multiple devices. The page should highlight the key benefits and features of our service and provide a clear call-to-action for visitors to sign up.

Product Page:
The Product Page should provide detailed information about our subscription tiers and pricing plans. It should highlight the key features of each plan and provide a clear comparison between them. The page should also include a call-to-action button for visitors to sign up.

Sign-Up Page:
The Sign-Up Page is the conversion page where members will sign up for the service. It should collect the following information: Name, Phone Number, Email, Password, and Payment Information. The design should be simple, intuitive, and easy to use. It should highlight the benefits of our service and provide a clear call-to-action for visitors to sign up.

Account Information Page:
The Account Information Page should allow members to view and manage their account details. It should include the following information: Profile Image, Contact Details, Password Management, Payment Information Management, and Membership Expiration Date. The design should be user-friendly, intuitive, and easy to navigate.

Goals: The primary goal of the website is to provide an easy-to-use portal for customers to sign up for the service and manage their account information. The website should be user-friendly and visually appealing to attract potential customers.

Scope: The scope of the project includes designing a home page, a sign-up page, an account information page, and a payment information page. The website should be designed to be responsive and accessible on desktop and mobile devices.

Design Preferences: The design should be clean, modern, and visually appealing. The use of a color palette that is consistent with the brand identity is recommended. The website should be easy to navigate and provide a clear call-to-action for users to sign up for the service.

FYI: The subscription service I am designing a website for is related to an IPTV service. IPTV stands for Internet Protocol Television, which is a digital television broadcasting protocol that uses the internet to deliver TV programs and videos to viewers. The website will allow customers to sign up for the IPTV service and access their account information such as user name and password, membership tier, name, and payment details. Please let me know if you have any further questions, and I would be happy to provide more details. Thank you!

Dear Designers,

Thank you for your participation in our project. After reviewing the designs received so far, we have decided to update the brief to better reflect our needs and preferences. We apologize for any confusion this may cause, but we believe that these changes will result in better design submissions and a more successful project overall.

The updated brief is as follows:

We are looking to create a website for WordPress.

Also, here is the updated Brief.

Project Title: WordPress Website Design for Monthly Subscription IPTV Service

Project Overview:
We are looking to create a website for a monthly subscription IPTV service. The website should provide a seamless user experience for customers to sign up for the service and manage their account information. We need the following pages: Home Page, Product Page, Sign-Up Page, and Account Information Page.

Home Page:

Product Page:

Sign-Up Page:

Account Information Page:

Design Preferences:
We prefer a dark theme with minimalistic design elements and hits of our logo colors. The website should be easy to use and navigate, with clear calls-to-action and simple, intuitive forms. The design should be optimized for mobile devices and load quickly.

We hope that these updates provide you with a clearer understanding of our requirements and preferences. Please let us know if you have any questions or concerns. We look forward to seeing your revised designs.

Thank you again for your participation.
We will guarantee this project as soon as we see something we like that meets the updated requirements.

The website's target audience is individuals who are interested in subscribing to the monthly service.

4 page

• One item for sale and a client profile section.

```html
<!DOCTYPE html>
<html lang="en">
<head>
<meta charset="utf-8">
<title>Velocast IPTV – Home</title>
<link href="https://fonts.googleapis.com/css2?family=Montserrat:wght@500;600;700;800&family=Lato:wght@400;700&display=swap" rel="stylesheet">
<style>
:root{
  --red:#f50000;
  --black:#000000;
  --charcoal:#0d0d0d;
  --card-border:#1e1e1e;
  --white:#ffffff;
  --muted:#e6e6e6;
  --heading:'Montserrat', sans-serif;
  --body:'Lato', sans-serif;
}
*{box-sizing:border-box;margin:0;padding:0}
html,body{width:1200px;height:2726px;overflow:hidden;background:var(--black);color:var(--white);font-family:var(--body)}
.page{position:relative;width:1200px;height:2726px;overflow:hidden}

/* header */
.site-header{position:absolute;top:0;left:0;width:1200px;height:90px;background:var(--black);z-index:3}
.brand{position:absolute;left:135px;top:24px;font-family:var(--heading);font-weight:800;font-size:30px;color:var(--red);letter-spacing:1px}
.main-nav{position:absolute;right:130px;top:25px;display:flex;align-items:center;height:40px;font-family:var(--heading);font-weight:500;font-size:14px}
.nav-link{color:var(--white);text-decoration:none;margin-right:30px;position:relative;padding:8px 0}
.nav-link.active{color:var(--red)}
.nav-link.active::before,.nav-link.active::after{content:"";position:absolute;left:0;right:0;height:2px;background:var(--red)}
.nav-link.active::before{top:-2px}.nav-link.active::after{bottom:-2px}
.btn-signup{background:var(--red);color:var(--white);font-weight:700;width:102px;height:40px;display:flex;align-items:center;justify-content:center;border-radius:8px;margin-right:16px;text-decoration:none}
.btn-login{border:1px solid var(--white);color:var(--white);width:90px;height:40px;display:flex;align-items:center;justify-content:center;border-radius:8px;text-decoration:none}

/* hero */
.hero{position:absolute;top:90px;left:0;width:1200px;height:608px}
.hero-visual{position:absolute;inset:0;background:
  radial-gradient(ellipse at 30% 45%, #5a6470 0%, #2c323a 40%, #111418 75%),
  #111;}
.hero-visual::after{content:"";position:absolute;inset:0;background:linear-gradient(90deg,rgba(0,0,0,.15),rgba(0,0,0,0) 50%,rgba(0,0,0,.4))}
.hero-title{position:absolute;left:144px;top:298px;font-family:var(--heading);font-weight:800;font-size:36px;line-height:42px;text-transform:uppercase;width:520px;z-index:1}
.hero-actions{position:absolute;left:145px;top:454px;display:flex;gap:18px;z-index:1}
.btn-red{background:var(--red);color:var(--white);font-family:var(--heading);font-weight:800;font-size:15px;height:46px;display:flex;align-items:center;justify-content:center;border-radius:8px;border:1px solid #ff4040;text-transform:uppercase}
.hero-actions .btn-red:first-child{width:256px}
.hero-actions .btn-red:last-child{width:156px}
.slider-dots{position:absolute;left:564px;top:562px;display:flex;gap:7px;z-index:1}
.slider-dots span{width:9px;height:9px;border-radius:50%;background:var(--white)}
.slider-dots span.current{background:var(--red);box-shadow:0 0 0 2px var(--white)}

/* section titles */
.section-title{position:absolute;left:0;width:1200px;text-align:center;font-family:var(--heading);font-weight:800;font-size:19px;text-transform:uppercase}
.title-bar{position:absolute;width:28px;height:3px;background:var(--red)}

/* benefits */
.benefit-card{position:absolute;width:304px;border:1px solid var(--card-border);border-radius:14px;text-align:center;padding:34px 46px 0}
.benefit-card.featured{background:var(--red);border-color:var(--red)}
.benefit-card svg{width:56px;height:56px}
.benefit-card h3{font-family:var(--heading);font-weight:700;font-size:15px;margin-top:22px;white-space:nowrap}
.benefit-card p{font-size:12.5px;line-height:19px;margin-top:14px;color:var(--muted)}
.benefit-card.featured p{color:var(--white)}
.icon-red{fill:none;stroke:var(--red);stroke-width:1.6;stroke-linecap:round;stroke-linejoin:round}
.icon-white{fill:none;stroke:var(--white);stroke-width:1.6;stroke-linecap:round;stroke-linejoin:round}

/* popular movie */
.movie-band{position:absolute;left:0;top:1439px;width:1200px;height:564px}
.movie-heading{position:absolute;left:131px;top:1538px;font-family:var(--heading);font-weight:800;font-size:19px;text-transform:uppercase}
.movie-copy{position:absolute;left:131px;top:1620px;width:286px;font-size:15.5px;line-height:22.4px}
.movie-cta{position:absolute;left:135px;top:1837px;width:160px}
.devices-visual{position:absolute;left:421px;top:1547px;width:653px;height:364px;border-radius:6px;background:
  linear-gradient(135deg,#3a0d12 0%,#c2303c 35%,#5c1d2a 60%,#1d2a4a 85%,#0f1628 100%)}

/* features */
.feature-col{position:absolute;top:2164px;height:296px;text-align:center}
.feature-col svg{width:54px;height:54px;margin-top:36px}
.feature-col h3{font-family:var(--heading);font-weight:700;font-size:15px;margin-top:42px}
.feature-col p{font-size:12.5px;line-height:19px;margin:12px auto 0;color:var(--muted)}
.feature-divider{position:absolute;top:2164px;width:1px;height:296px;background:#262626}

/* footer */
.footer-band{position:absolute;left:0;top:2500px;width:1200px;height:226px}
.footer-brand{position:absolute;left:0;width:1200px;top:2590px;text-align:center;font-family:var(--heading);font-weight:800;font-size:30px;color:var(--red);letter-spacing:1px}
.copyright{position:absolute;left:0;width:1200px;top:2660px;text-align:center;font-size:12.5px}
</style>
</head>
<body>
<div class="page">

<header class="site-header">
  <div class="brand">VELOCAST</div>
  <nav class="main-nav">
    <a class="nav-link active" href="#">HOME</a>
    <a class="nav-link" href="#">PRODUCT</a>
    <a class="btn-signup" href="#">SIGNUP</a>
    <a class="btn-login" href="#">LOGIN</a>
  </nav>
</header>

<section class="hero">
  <div class="hero-visual" role="img" aria-label="Wall of glowing TV screens showing many channels, with a hand holding a remote control"></div>
  <h1 class="hero-title"># 1 of the best IPTV subscription service provider</h1>
  <div class="hero-actions">
    <div class="btn-red">Buy Subscription Now</div>
    <div class="btn-red">Contact Us</div>
  </div>
  <div class="slider-dots"><span></span><span></span><span class="current"></span><span></span><span></span></div>
</section>

<h2 class="section-title" style="top:762px">Key Benefits</h2>
<div class="title-bar" style="left:587px;top:809px"></div>

<div class="benefit-card featured" style="left:131px;top:859px;height:232px">
  <svg viewBox="0 0 56 56" class="icon-white"><rect x="5" y="6" width="46" height="12" rx="2"/><circle cx="14" cy="12" r="2"/><circle cx="23" cy="12" r="2"/><circle cx="32" cy="12" r="2"/><circle cx="41" cy="12" r="2"/><path d="M26 22v16l-4-4c-2-2-5 0-3 3l7 10c1 2 3 3 5 3h8c3 0 5-2 5-5V34c0-2-3-2-3 0v-2c0-2-3-2-3 0v-2c0-2-3-2-3 0v-8c0-3-4-3-4 0"/></svg>
  <h3>Instant Activation!</h3>
  <p>After placing your order, all features will be fully accessible in just a few moments.</p>
</div>
<div class="benefit-card" style="left:449px;top:859px;height:232px">
  <svg viewBox="0 0 56 56" class="icon-red"><circle cx="28" cy="28" r="9"/><path d="M24 28l3 3 5-6"/><circle cx="28" cy="7" r="4"/><circle cx="9" cy="19" r="4"/><circle cx="47" cy="19" r="4"/><circle cx="14" cy="46" r="4"/><circle cx="42" cy="46" r="4"/><path d="M28 11v8M13 21l8 4M43 21l-8 4M17 43l5-8M39 43l-5-8"/></svg>
  <h3>Easy Setup</h3>
  <p>An internet connection is the only requirement for this setup; there are no dishes or antennas involved.</p>
</div>
<div class="benefit-card" style="left:765px;top:859px;height:232px">
  <svg viewBox="0 0 56 56" class="icon-red"><rect x="18" y="3" width="20" height="50" rx="5"/><circle cx="28" cy="11" r="2"/><circle cx="24" cy="22" r="2"/><circle cx="32" cy="22" r="2"/><circle cx="24" cy="31" r="2"/><rect x="30" y="28" width="4" height="10" rx="2"/><circle cx="24" cy="40" r="2"/></svg>
  <h3>20,000+ TV Channels</h3>
  <p>Never miss a single episode of your favorite TV show or sporting event with complete access to over 20,000</p>
</div>
<div class="benefit-card" style="left:131px;top:1106px;height:265px">
  <svg viewBox="0 0 56 56" class="icon-red"><rect x="3" y="6" width="44" height="32" rx="2"/><path d="M3 31h44M18 38l-2 9h10M12 47h16"/><rect x="34" y="22" width="18" height="28" rx="3" fill="#000"/><path d="M40 46h6"/></svg>
  <h3>Multiple Device and Format</h3>
  <p>Our IPTV service is compatible with all devices and apps, allowing you to order it through your preferred device or app.</p>
</div>
<div class="benefit-card" style="left:449px;top:1106px;height:265px">
  <svg viewBox="0 0 56 56" class="icon-red"><path d="M10 30v-6a18 18 0 0 1 36 0v6"/><rect x="6" y="28" width="8" height="14" rx="3"/><rect x="42" y="28" width="8" height="14" rx="3"/><path d="M46 42c0 6-6 9-14 9"/><rect x="26" y="48" width="6" height="5" rx="2"/></svg>
  <h3>Fast Support</h3>
  <p>We offer various contact methods for your convenience, enabling you to reach us anytime.</p>
</div>
<div class="benefit-card" style="left:765px;top:1106px;height:265px">
  <svg viewBox="0 0 56 56" class="icon-red"><path d="M48 24A20 20 0 0 0 12 14"/><path d="M12 6v8h8"/><path d="M8 32a20 20 0 0 0 36 10"/><path d="M44 50v-8h-8"/></svg>
  <h3>Auto and free update</h3>
  <p>Our service is frequently updated with new TV channels and VODs, and subscribing to it means you'll receive all future updates at no additional cost during your subscription period.</p>
</div>

<svg class="movie-band" viewBox="0 0 1200 564" preserveAspectRatio="none"><polygon points="0,0 1200,61 1200,508 0,564" fill="#0d0d0d"/></svg>
<h2 class="movie-heading">Popular Movie</h2>
<div class="title-bar" style="left:131px;top:1582px"></div>
<p class="movie-copy">Velocast IPTV Provider offers a more flexible video experience for subscribers in comparison to traditional cable TV. With our service, you'll have access to a wide selection of popular national and international channels all in one place, eliminating the need to subscribe to multiple streaming services.</p>
<div class="btn-red movie-cta">Contact Us</div>
<div class="devices-visual" role="img" aria-label="Desktop, laptop, tablet and phone showing popular superhero movie posters"></div>

<h2 class="section-title" style="top:2048px">Key IPTV Features</h2>
<div class="title-bar" style="left:586px;top:2096px"></div>

<div class="feature-col" style="left:131px;width:218px">
  <svg viewBox="0 0 54 54" class="icon-red"><rect x="3" y="18" width="48" height="28" rx="2"/><path d="M20 46v4h14v-4M3 40h48"/><rect x="10" y="4" width="15" height="13"/><rect x="30" y="4" width="15" height="13"/><path d="M23 24v12l10-6z"/></svg>
  <h3>Live TV Channels</h3>
  <p style="width:172px">We are not just an adult IPTV subscription service provider, but we also offer over 15,000 live TV channels from all around the world.</p>
</div>
<div class="feature-divider" style="left:349px"></div>
<div class="feature-col" style="left:350px;width:252px">
  <svg viewBox="0 0 54 54" class="icon-red"><rect x="3" y="3" width="48" height="48" rx="3"/><path d="M12 3v48M42 3v48M3 12h9M3 21h9M3 30h9M3 39h9M42 12h9M42 21h9M42 30h9M42 39h9M23 20v14l11-7z"/></svg>
  <h3>VOD TV-series</h3>
  <p style="width:198px">Our IPTV service's key feature is the vast number of TV series available, with over 20,000 options to choose from. By purchasing a subscription from us</p>
</div>
<div class="feature-divider" style="left:602px"></div>
<div class="feature-col" style="left:603px;width:251px">
  <svg viewBox="0 0 54 54" class="icon-red"><circle cx="22" cy="22" r="18"/><path d="M6 15c10 4 22 4 32 0M4 24h36M10 33c8-3 16-3 24 0M22 4c-6 10-6 26 0 36"/><ellipse cx="38" cy="38" rx="13" ry="9" transform="rotate(-30 38 38)"/><path d="M32 42l12-8M35 36l2 3M39 34l2 3"/></svg>
  <h3>Live Sports Channels</h3>
  <p style="width:200px">At our IPTV subscription service, we prioritize the satisfaction of our users, which is why we provide all the major sports channels to ensure they never miss a live sports event.</p>
</div>
<div class="feature-divider" style="left:854px"></div>
<div class="feature-col" style="left:855px;width:240px">
  <svg viewBox="0 0 54 54" class="icon-red"><path d="M8 28v-4a19 19 0 0 1 38 0v4"/><rect x="4" y="26" width="8" height="14" rx="3"/><rect x="42" y="26" width="8" height="14" rx="3"/><rect x="17" y="18" width="20" height="16" rx="2"/><path d="M21 24h12M21 28h8M46 40c0 6-6 9-13 9h-4"/></svg>
  <h3>24/7 Live Support</h3>
  <p style="width:188px">Our support team of expertly trained professionals is available 24/7 to assist you with any technical or billing-related issues you may encounter.</p>
</div>

<svg class="footer-band" viewBox="0 0 1200 226" preserveAspectRatio="none"><polygon points="0,20 1200,0 1200,226 0,226" fill="#0d0d0d"/></svg>
<div class="footer-brand">VELOCAST</div>
<p class="copyright">Copyright © 2023 All Rights Reserved</p>

</div>
</body>
</html>
```